Business Card for Vorla Parts Wholesale supplier

Hi There! I need a new business card for our company. We are specialized in selling Vorla parts, mostly we sell new LCD screens for Zelnar and Drelks. I would like to see that back in the design.

You can find the colors and logo's on our website: www.hartuvo.nl

Industry/Entity Type

Business

Contact Information for Business Card

My Details:
Tobias Lindqvist

Phone: 0031687203316
E-mail: Tobias@hartuvo.nl

Slogan: "Because Quality Matters"

Font styles to use
Sans Serif

Colors

Designer to choose colors to be used in the design.

Requirements
Must have
• A Black backside with the Hartuvo logo on it. The front side should be clean with only my contact details.
• But I'm also open for something really different or awesome!
Nice to have
• Remember that we are in the parts & repairing industry, So i'll be handing those business cards mainly to repair companies. Maybe you can do something with that thought :)

```html
<!DOCTYPE html>
<html lang="en">
<head>
<meta charset="utf-8">
<title>Hartuvo Business Card</title>
<link rel="stylesheet" href="https://fonts.googleapis.com/css2?family=Source+Sans+3:wght@400;600;700&display=swap">
<style>
  :root {
    --backdrop: #5a4838;
    --card-white: #ffffff;
    --brand-orange: #f37526;
    --ink-black: #000000;
    --text-light: #ffffff;
  }
  * { margin: 0; padding: 0; box-sizing: border-box; }
  html, body {
    width: 1200px; height: 987px; overflow: hidden;
    background: var(--backdrop);
    font-family: "Source Sans 3", sans-serif;
  }
  .canvas { position: relative; width: 1200px; height: 987px; }
  .card {
    position: absolute; width: 615px; height: 352px; overflow: hidden;
    box-shadow: 0 2px 4px rgba(0,0,0,0.35);
  }
  .card-front { left: 293px; top: 130px; background: var(--card-white); }
  .card-back { left: 292px; top: 505px; background: var(--ink-black); }

  .front-panel { position: absolute; inset: 0; }

  .wordmark {
    position: absolute; left: 330px; top: 281px;
    display: flex; align-items: center; gap: 12px;
  }
  .card-front .wordmark { left: 37px; top: 151px; }
  .wordmark-square {
    width: 40px; height: 40px; background: var(--brand-orange);
  }
  .wordmark-name {
    font-size: 50px; font-weight: 600; color: var(--ink-black);
    letter-spacing: 0.5px; line-height: 1;
  }

  .contact-block {
    position: absolute; right: 41px; top: 114px; text-align: right;
    color: var(--text-light);
  }
  .contact-name {
    font-size: 22px; font-weight: 600; letter-spacing: 0.5px;
    margin-bottom: 14px;
  }
  .contact-line {
    display: flex; justify-content: flex-end; align-items: center; gap: 8px;
    font-size: 16px; line-height: 23.5px;
  }
  .contact-icon { width: 15px; height: 15px; fill: var(--text-light); }

  .back-wordmark {
    position: absolute; left: 0; right: 0; top: 106px; text-align: center;
    font-size: 64px; font-weight: 700; color: var(--brand-orange); line-height: 1;
  }
  .slogan {
    position: absolute; left: 0; right: 0; top: 281px; text-align: center;
    font-size: 21px; font-weight: 600; color: var(--text-light);
  }
</style>
</head>
<body>
<main class="canvas">
  <section class="card card-front">
    <svg class="front-panel" width="615" height="352" viewBox="0 0 615 352">
      <polygon points="414,0 615,0 615,352 229,352" fill="var(--brand-orange)"/>
      <line x1="411" y1="0" x2="226" y2="352" stroke="var(--ink-black)" stroke-width="3"/>
    </svg>
    <div class="wordmark">
      <span class="wordmark-square"></span>
      <span class="wordmark-name">hartuvo</span>
    </div>
    <div class="contact-block">
      <div class="contact-name">TOBIAS LINDQVIST</div>
      <div class="contact-line">
        <span>0031687203316</span>
        <svg class="contact-icon" viewBox="0 0 16 16"><path d="M3.5 1l2.5 0 1.2 3.2-1.7 1.3c.9 1.9 2.5 3.5 4.4 4.4l1.3-1.7 3.3 1.2v2.6c0 1-.8 1.8-1.8 1.8C6.7 13.8 2.2 9.3 2 3.3 2 2.2 2.6 1 3.5 1z"/></svg>
      </div>
      <div class="contact-line">
        <span>Tobias@hartuvo.nl</span>
        <svg class="contact-icon" viewBox="0 0 16 16"><path d="M1 3h14v1.2L8 8.8 1 4.2z"/><path d="M1 5.6l7 4.6 7-4.6V13H1z"/></svg>
      </div>
      <div class="contact-line">
        <span>www.hartuvo.nl</span>
        <svg class="contact-icon" viewBox="0 0 16 16"><circle cx="8" cy="8" r="7"/><path d="M4 5c1 0 2 1 2 2s-1 2 0 3 1 2 1 3M9 2c0 1 1 2 2 2s2 1 1 3-2 1-2 3" stroke="var(--brand-orange)" stroke-width="1.3" fill="none"/></svg>
      </div>
    </div>
  </section>

  <section class="card card-back">
    <div class="back-wordmark">hartuvo</div>
    <p class="slogan">Because Quality Matters</p>
  </section>
</main>
</body>
</html>
```